Consulting Practice for Charities Needs A Brochure Deisgn

Hi! We need a tri-fold brochure for a Washington, DC based consulting practice that works with charities (NGOs, Associations, etc.) and wealthy donors (philanthropists). Our company, Morrow Civic Advisors, helps nonprofits to implement practices that maximize organizational efficiency and effectiveness - by working directly with board members and staff.
Our clients are well educated and quite sophisticated (some charities are international with multi-million dollar budgets, while others are quite local and small) This brochure will be handed to them by some of our 'referral partners' (law firms, accountants and even governmental agencies) in addition to being given out during our presentations. We draw inspiration from nature and would like to somehow include a "natural / eco-friendly" feel to the piece, including natural colors .... that being said, not in any way "folksy" - it must be sophisticated.

Target Market(s)

nonprofit executive directors, board chairs, wealth holders (philanthropists)

Industry/Entity Type

Consulting

Requirements
Must have
• I uploaded a word file with content (text) - most of that needs to be on the brochure ... but ... if it looks too crowded, let me know and I'll reduce
Nice to have
• pop-out quotes (maybe from testimonials??), nature - theme of some kind but also photo of boardroom (links to samples are like are uploaded in a word doc below)
Should not have
• nothing cute ... nothing too feminine

```html
<!DOCTYPE html>
<html lang="en">
<head>
<meta charset="utf-8">
<title>Morrow Civic Advisors – Tri-fold Brochure</title>
<link rel="stylesheet" href="https://fonts.googleapis.com/css2?family=Lusitana:wght@400;700&family=Zilla+Slab:wght@600;700&family=Source+Sans+3:wght@400;600&display=swap">
<style>
  :root {
    --canvas: #d4d5d7;
    --purple: #8078bc;
    --purple-ink: #7a71b6;
    --green: #8cc43c;
    --orange: #f7921e;
    --ink: #444446;
    --ink-dark: #1f1f22;
    --white: #ffffff;
  }
  * { box-sizing: border-box; margin: 0; padding: 0; }
  html, body { width: 1200px; height: 970px; overflow: hidden; background: var(--canvas); }
  .brochure {
    position: absolute; left: 63px; top: 72px; width: 1073px; height: 833px;
    overflow: hidden; background: var(--white);
    font-family: "Lusitana", Georgia, serif; color: var(--ink);
  }
  .backdrop { position: absolute; inset: 0; }
  .abs { position: absolute; }

  .headline {
    left: 392px; top: 62px; width: 272px; text-align: center;
    color: var(--white); font-size: 26px; line-height: 31.5px;
    text-shadow: 0 1px 4px rgba(0,0,0,.7);
  }
  .headline .lead { font-family: "Lusitana", Georgia, serif; font-weight: 400; }
  .headline .focus { font-family: "Zilla Slab", Georgia, serif; font-weight: 700; }

  .section-title {
    left: 37px; top: 248px; font-family: "Zilla Slab", Georgia, serif;
    font-weight: 700; font-size: 22px; color: var(--purple-ink);
  }
  .copy { left: 37px; width: 292px; font-size: 12.8px; line-height: 15.9px; letter-spacing: .2px; }
  .copy h3 {
    font-family: "Source Sans 3", Arial, sans-serif; font-weight: 400;
    font-size: 13.8px; color: var(--ink-dark); line-height: 16px; letter-spacing: 0;
  }
  .copy--org { top: 281px; }
  .copy--private { top: 557px; }

  .quote {
    background: var(--green); color: var(--white); text-align: center;
    padding: 0 18px; font-size: 12.4px; line-height: 15.8px; letter-spacing: .2px;
  }
  .quote .who { font-family: "Zilla Slab", Georgia, serif; font-weight: 700; font-size: 12.4px; line-height: 16px; letter-spacing: .1px; }
  .quote--journalist { left: 30px; top: 659px; width: 283px; height: 156px; padding-top: 30px; }
  .quote--philanthropist { left: 399px; top: 290px; width: 282px; height: 340px; padding-top: 41px; }
  .quote--chair { left: 759px; top: 593px; width: 283px; height: 222px; padding-top: 35px; }

  .quote-mark {
    width: 49px; height: 49px; border-radius: 50%; background: var(--white);
    display: flex; align-items: center; justify-content: center;
  }
  .quote-mark--journalist { left: 147px; top: 635px; }
  .quote-mark--philanthropist { left: 516px; top: 266px; }
  .quote-mark--chair { left: 876px; top: 569px; }

  .brand {
    left: 779px; top: 92px; width: 294px; text-align: center;
    display: flex; flex-direction: column; align-items: center; gap: 8px;
  }
  .brand .mark { width: 14px; height: 14px; background: var(--purple); }
  .brand .name { font-size: 22px; color: var(--purple-ink); letter-spacing: .5px; }

  .services-title {
    left: 779px; top: 153px; width: 294px; text-align: center;
    font-family: "Source Sans 3", Arial, sans-serif; font-weight: 400;
    font-size: 28px; color: var(--green);
  }
  .services { left: 747px; top: 199px; width: 326px; list-style: none; font-size: 14px; line-height: 19.9px; letter-spacing: .2px; }
  .services li { position: relative; padding-left: 15px; }
  .services li::before {
    content: ""; position: absolute; left: 1px; top: 8px; width: 4px; height: 4px;
    border-radius: 50%; background: var(--green);
  }
  .services ul { list-style: none; margin-left: 32px; }
  .services ul li { padding-left: 10px; }
  .services ul li::before { background: var(--orange); left: 0; }

  .web {
    left: 357px; top: 798px; width: 378px; text-align: center;
    color: var(--white); font-size: 16px; letter-spacing: .3px;
  }
</style>
</head>
<body>
<main class="brochure">
  <svg class="backdrop" width="1073" height="833" viewBox="0 0 1073 833">
    <defs>
      <linearGradient id="lakeScene" x1="0" y1="0" x2="0" y2="1">
        <stop offset="0" stop-color="#e9ecef"/>
        <stop offset=".35" stop-color="#b7c1bf"/>
        <stop offset=".55" stop-color="#2f4a34"/>
        <stop offset=".75" stop-color="#3b4549"/>
        <stop offset="1" stop-color="#1d2426"/>
      </linearGradient>
      <linearGradient id="forestTop" x1="0" y1="0" x2="0" y2="1">
        <stop offset="0" stop-color="#9fc3e4"/>
        <stop offset=".25" stop-color="#e4ecf2"/>
        <stop offset=".45" stop-color="#2e4a2f"/>
        <stop offset=".65" stop-color="#3c5a3a"/>
        <stop offset=".8" stop-color="#6e7e85"/>
        <stop offset="1" stop-color="#2c3436"/>
      </linearGradient>
      <linearGradient id="purpleFade" x1="0" y1="0" x2="0" y2="1">
        <stop offset=".8" stop-color="#8078bc"/>
        <stop offset="1" stop-color="#8078bc" stop-opacity="0"/>
      </linearGradient>
      <linearGradient id="whiteFadeLeft" x1="0" y1="0" x2="0" y2="1">
        <stop offset=".85" stop-color="#ffffff"/>
        <stop offset="1" stop-color="#ffffff" stop-opacity="0"/>
      </linearGradient>
      <linearGradient id="whiteFadeRight" x1="0" y1="0" x2="0" y2="1">
        <stop offset=".82" stop-color="#ffffff"/>
        <stop offset="1" stop-color="#ffffff" stop-opacity="0"/>
      </linearGradient>
    </defs>

    <g role="img" aria-label="Photograph of a calm northern lake with reeds and pine forest along the shore">
      <rect x="0" y="200" width="1073" height="633" fill="url(#lakeScene)"/>
    </g>
    <rect x="357" y="150" width="358" height="400" fill="url(#purpleFade)"/>
    <rect x="0" y="200" width="357" height="450" fill="url(#whiteFadeLeft)"/>
    <rect x="715" y="0" width="358" height="600" fill="url(#whiteFadeRight)"/>

    <g role="img" aria-label="Photograph of a forest lake under a blue sky with white clouds">
      <path d="M0 0 H715 V160 C660 205 610 250 545 250 C480 250 420 228 357 222 C280 210 190 198 100 214 C60 222 25 234 0 244 Z" fill="url(#forestTop)"/>
    </g>
    <path d="M0 243 C80 214 200 198 320 212 L320 215 C200 205 90 222 0 260 Z" fill="var(--orange)"/>
    <path d="M372 226 C470 254 600 262 715 150 L715 172 C610 258 480 258 372 226 Z" fill="var(--green)"/>

    <rect x="0" y="783" width="1073" height="5" fill="var(--green)"/>
    <rect x="0" y="788" width="1073" height="45" fill="var(--purple)"/>
  </svg>

  <h1 class="abs headline">
    <span class="lead">Guiding Responsible Philanthropy</span><br>
    <span class="focus">Improving Board Governance</span>
  </h1>

  <h2 class="abs section-title">What we do:</h2>
  <section class="abs copy copy--org">
    <h3>Organizational Clients</h3>
    <p>20th century developmental psychologist Emil Hartmann asserted that for individuals, conflict and crisis are positive and necessary; they are "sources of growth, strength, and commitment." We believe the same can be true of organizations. MCA helps nonprofits manage change and emerge triumphantly. Through coaching, we help organizations implement practices to maximize efficiency and effectiveness - whether preparing for transition, coping with chaos, or simply pursuing continued high performance - by working directly with board members and staff.</p>
    <p>Our methods are informed by research and honed by over 20 years of practice.</p>
  </section>
  <section class="abs copy copy--private">
    <h3>Private Clients</h3>
    <p>MCA philanthropic counsel helps individuals adopt impactful practices in their charitable endeavors.</p>
  </section>

  <blockquote class="abs quote quote--philanthropist">
    <p class="who">Grant Ellison, CTFA (Client, Philanthropist)</p>
    <p>“I’ve had the honor and distinct privilege of working with Dana through her Board Coaching &amp; Training program. The board self-assessment process is thorough, insightful and necessary, if like me, you are challenged with finding the right organization to align with. Leveraging her expertise, guidance and deep connections throughout the Non-Profit space, Dana carefully screened several organizations as potential candidates, and went so far as to arrange introductory meetings with a select few. The entire process was educational, and an exceptional experience.”</p>
  </blockquote>
  <blockquote class="abs quote quote--journalist">
    <p class="who">Owen Pritchard (Client, Journalist and Broadcaster)</p>
    <p>“Dana is at forefront of the new era of responsible philanthropy … Most importantly, she has the rare ability to take a vision and turn it into a coherent plan of action.”</p>
  </blockquote>
  <blockquote class="abs quote quote--chair">
    <p class="who">Ruth Calder (Past Chairman, Northern Society for Arts and Health)</p>
    <p>“I wish you could have heard the board’s comments. They were unanimously and warmly enthusiastic, saying it was the best thing we, as a board, have ever done… Thank you for the thought and combination of emotional and intellectual intelligence that you brought to the presentation.”</p>
  </blockquote>

  <div class="abs quote-mark quote-mark--journalist" aria-hidden="true"><svg width="26" height="20" viewBox="0 0 26 20"><path d="M10 2 C4 4 1 8 1 13 a4 4 0 1 0 8 0 a4 4 0 0 0 -4 -4 C5 7 7 5 11 4 Z M24 2 C18 4 15 8 15 13 a4 4 0 1 0 8 0 a4 4 0 0 0 -4 -4 C19 7 21 5 25 4 Z" fill="var(--green)"/></svg></div>
  <div class="abs quote-mark quote-mark--philanthropist" aria-hidden="true"><svg width="26" height="20" viewBox="0 0 26 20"><path d="M10 2 C4 4 1 8 1 13 a4 4 0 1 0 8 0 a4 4 0 0 0 -4 -4 C5 7 7 5 11 4 Z M24 2 C18 4 15 8 15 13 a4 4 0 1 0 8 0 a4 4 0 0 0 -4 -4 C19 7 21 5 25 4 Z" fill="var(--green)"/></svg></div>
  <div class="abs quote-mark quote-mark--chair" aria-hidden="true"><svg width="26" height="20" viewBox="0 0 26 20"><path d="M10 2 C4 4 1 8 1 13 a4 4 0 1 0 8 0 a4 4 0 0 0 -4 -4 C5 7 7 5 11 4 Z M24 2 C18 4 15 8 15 13 a4 4 0 1 0 8 0 a4 4 0 0 0 -4 -4 C19 7 21 5 25 4 Z" fill="var(--green)"/></svg></div>

  <div class="abs brand">
    <span class="mark"></span>
    <span class="name">Morrow Civic Advisors</span>
  </div>

  <h2 class="abs services-title">Services</h2>
  <ul class="abs services">
    <li>Board and Senior Staff Coaching</li>
    <li>Workshops, Seminars and Retreats<br>including:
      <ul>
        <li>Roles &amp; Responsibilities</li>
        <li>Fundraising</li>
        <li>Succession Planning</li>
        <li>Board Self-Assessments</li>
        <li>Strategic Planning</li>
        <li>Board Recruitment Training</li>
        <li>Communications Development</li>
        <li>Grassroots Advocacy</li>
        <li>Mergers &amp; Acquisitions</li>
      </ul>
    </li>
    <li>Philanthropic Counsel</li>
    <li>Board Placement</li>
    <li>Board Member Recruitment</li>
    <li>Board Retreat Planning &amp; Facilitation</li>
  </ul>

  <p class="abs web">MorrowCivicAdvisors.com</p>
</main>
</body>
</html>
```